PixelHarbor Rangers (Ledgerline Nova)
A website dedicated to crypto education. We are a new company focused on blockchain edutainment (education and interesting and entertaining content about the blockchain space). We want a fun, clean/minimalist and modern website that is made up of an education platform which could be a website in it’s own right. It will be the reference point for our users/community for all of our other blockchain based content in the PHR website ecosystem which will be covering; crypto news, digital asset investing (including a technical and fundamental analysis subscription service), blockchain business solutions and an NFT section that will cover creative art projects (art, music, gaming and more). To feature a logins and payment system which may need a shopping basket set up for tutorial/educational platform that is accessed via the website, NFT page with sub-categories: education and NFT and metaverse/virtual world and merchandise shopping page which is Web 3.0 enabled (able to link to a VeloPurse, Kindle Vault etc , digital asset education page featuring blog and newsletter subscriptions links, A social media page where people can access videos, podcasts and our presence on other platforms such as Chirplo, Snapmora, Huddlex, Wirepost etc.
Number of Pages Required
5+ page
Look and feel

```html
<!DOCTYPE html>
<html lang="en">
<head>
<meta charset="utf-8">
<title>PixelHarbor Rangers — Blockchain Edutainment</title>
<link rel="stylesheet" href="https://fonts.googleapis.com/css2?family=Pixelify+Sans:wght@500;700&family=Space+Mono:wght@400;700&display=swap">
<style>
:root{
  --night:#14072c;
  --night-deep:#0f0524;
  --plum:#1d0b3a;
  --card:#210b45;
  --violet:#8a1ff0;
  --violet-bright:#a23cff;
  --magenta:#e010e8;
  --glow-green:#dcffd2;
  --text:#ffffff;
  --muted:#d8d0e8;
  --faded:#3a2560;
  --pixel:"Pixelify Sans", monospace;
  --mono:"Space Mono", monospace;
}
*{box-sizing:border-box;margin:0;padding:0}
html,body{width:1200px;height:4175px;overflow:hidden}
body{background:var(--night);color:var(--text);font-family:var(--mono);position:relative}
.abs{position:absolute}
.section{position:absolute;left:0;width:1200px}
.placeholder{position:absolute;border-radius:6px}

/* nav */
.site-header{top:0;height:80px}
.brand{left:50px;top:8px;font-family:var(--pixel);font-weight:700;font-size:24px;line-height:29px;text-align:center}
.nav-link{top:32px;font-size:13px;letter-spacing:.5px;color:#fff}
.nav-link.is-active{color:var(--violet-bright)}
.cart-btn{left:919px;top:16px;width:50px;height:50px;border-radius:50%;border:2px solid var(--violet);display:flex;align-items:center;justify-content:center}
.signup-btn{left:1000px;top:15px;width:148px;height:52px;border-radius:26px;border:2px solid var(--violet);color:var(--violet-bright);font-family:var(--pixel);font-size:19px;display:flex;align-items:center;justify-content:center;letter-spacing:1px}

/* hero */
.hero{top:0;height:640px;background:radial-gradient(ellipse at 50% 40%,#221040 0%,#170a30 70%)}
.hero-line{font-family:var(--pixel);font-weight:700;font-size:56px;line-height:70px;color:var(--glow-green);text-shadow:0 0 8px rgba(140,255,140,.45);letter-spacing:2px}
.earn-tab{left:1146px;top:235px;width:54px;height:170px;background:var(--magenta);display:flex;flex-direction:column;align-items:center;padding-top:14px;gap:12px}
.earn-tab span{writing-mode:vertical-rl;font-size:14px;letter-spacing:1px;font-weight:700}

/* ecosystem */
.ecosystem{top:640px;height:615px;background:var(--night-deep)}
.tab{font-family:var(--pixel);font-size:30px;top:78px}
.eco-card{top:165px;width:296px;height:345px;background:var(--card);border-radius:148px 148px 0 0;text-align:center;padding-top:40px}
.eco-card h3{font-family:var(--mono);font-size:17px;margin-top:20px;color:#fff}
.eco-card p{font-size:13px;line-height:24px;margin:14px 22px 0;color:var(--muted)}
.card-arrow{margin-top:22px}
.round-arrow{width:40px;height:40px;border-radius:50%;background:#fff;display:flex;align-items:center;justify-content:center}

/* creative art */
.creative{top:1255px;height:650px;background:linear-gradient(#1a0a38,#2a1552)}
.section-title{font-family:var(--pixel);font-weight:700;font-size:32px;text-align:center;width:1200px;left:0}
.section-sub{font-size:13px;line-height:24px;text-align:center;width:720px;left:240px;color:var(--muted)}
.side-label{font-family:var(--pixel);font-weight:700;font-size:24px;top:375px}
.dot{width:7px;height:7px;border-radius:50%;top:570px}

/* tutorial */
.tutorial{top:2655px;height:695px;background:linear-gradient(#14072c,#1a0a36)}
.tut-card{top:195px;width:302px;height:430px;background:#1d0a3b;text-align:center}
.tut-media{position:absolute;left:0;top:0;width:100%;height:193px;overflow:hidden}
.ribbon{position:absolute;right:0;top:0;width:90px;height:90px;background:linear-gradient(225deg,var(--violet) 50%,transparent 50%)}
.ribbon span{position:absolute;right:8px;top:8px;font-family:var(--pixel);font-size:17px;line-height:21px;text-align:right}
.tut-body{position:absolute;top:210px;left:0;width:100%}
.tut-tier{font-size:16px;font-weight:700}
.tut-card h4{font-size:15px;line-height:24px;margin:10px 20px 0}
.tut-card p{font-size:12px;line-height:24px;margin:12px 18px 0;color:var(--muted)}
.socials{display:flex;justify-content:center;gap:10px;margin-top:14px}
.socials span{font-size:11px;color:var(--violet-bright);font-weight:700}

/* digital asset */
.digital{top:3350px;height:470px;background:#1a0a36}
.btn{top:320px;height:54px;border-radius:27px;font-family:var(--pixel);font-size:19px;display:flex;align-items:center;justify-content:center}
.btn-primary{left:415px;width:208px;background:var(--violet)}
.btn-outline{left:633px;width:150px;border:2px solid var(--violet);color:var(--violet-bright)}

/* footer */
.site-footer{top:3820px;height:355px;background:var(--night-deep)}
.footer-brand{font-family:var(--pixel);font-weight:700;font-size:44px;letter-spacing:1px}
.footer-nav{top:150px;left:0;width:1200px;display:flex;justify-content:center;gap:40px;font-size:13px}
.pay-row{top:187px;left:0;width:1200px;display:flex;justify-content:center;gap:6px}
.pay-chip{width:48px;height:28px;background:#fff;color:#1d0b3a;font-size:9px;font-weight:700;display:flex;align-items:center;justify-content:center;border-radius:3px}
.wallet-row{top:232px;left:0;width:1200px;display:flex;justify-content:center;gap:18px;font-size:12px}
.wallet-row span{display:flex;align-items:center;gap:6px}
.wallet-row i{width:14px;height:14px;border-radius:50%;background:var(--violet);display:inline-block}
.copyright{top:290px;left:0;width:1200px;text-align:center;font-size:12px;line-height:22px}
.copyright em{font-style:normal;color:var(--violet-bright)}
</style>
</head>
<body>

<section class="section hero">
  <div class="placeholder" role="img" aria-label="White pixel ghost character" style="left:218px;top:140px;width:187px;height:210px;background:linear-gradient(#f4f4f8,#d8d8e2);border-radius:90px 90px 8px 8px"></div>
  <div class="abs hero-line" style="left:520px;top:175px">Just Because you<br>Can’t Hold It.</div>
  <div class="abs hero-line" style="left:200px;top:432px">Doesn’t Mean You<br>Can’t Own IT</div>
  <div class="placeholder" role="img" aria-label="White pixel ghost character" style="left:788px;top:390px;width:200px;height:220px;background:linear-gradient(#f4f4f8,#d8d8e2);border-radius:96px 96px 8px 8px"></div>
  <div class="abs earn-tab">
    <svg width="30" height="30" viewBox="0 0 30 30"><circle cx="15" cy="15" r="14" fill="#fff"/><circle cx="15" cy="15" r="7" fill="none" stroke="#e010e8" stroke-width="3"/></svg>
    <span>EARN TOKENS</span>
  </div>
</section>

<header class="section site-header">
  <div class="abs brand">PixelHarbor<br>Rangers</div>
  <a class="abs nav-link is-active" style="left:235px">HOME</a>
  <a class="abs nav-link" style="left:316px">PHR ECOSYSTEM</a>
  <a class="abs nav-link" style="left:471px">NFT ART</a>
  <a class="abs nav-link" style="left:578px">EDUCATION &amp; NFT</a>
  <a class="abs nav-link" style="left:745px">BLOG</a>
  <a class="abs nav-link" style="left:826px">CONTACT</a>
  <div class="abs cart-btn"><svg width="18" height="16" viewBox="0 0 18 16"><path d="M1 1h3l2 9h9l2-7H5" fill="none" stroke="#fff" stroke-width="2"/><circle cx="7" cy="14" r="1.6" fill="#fff"/><circle cx="14" cy="14" r="1.6" fill="#fff"/></svg></div>
  <div class="abs signup-btn">SIGN UP</div>
</header>

<section class="section ecosystem">
  <div class="abs tab" style="left:290px">PHR Ecosystem</div>
  <div class="abs" style="left:547px;top:80px;width:3px;height:36px;background:#fff"></div>
  <div class="abs tab" style="left:592px;color:var(--faded)">Community Ecosystem</div>

  <article class="abs eco-card" style="left:130px">
    <svg width="60" height="60" viewBox="0 0 60 60" fill="none" stroke="#fff" stroke-width="2"><circle cx="30" cy="30" r="13"/><text x="30" y="35" font-size="14" text-anchor="middle" fill="#fff" stroke="none" font-family="monospace">₿</text><path d="M30 4v10M30 46v10M4 30h10M46 30h10M12 12l7 7M41 41l7 7M48 12l-7 7M12 48l7-7"/></svg>
    <h3>Crypto News</h3>
    <p>Lorem ipsum dolor sit amet, consectetur adipiscing elit, sed do eiusmod tempor incididunt ut labore et dolore magna aliqua. Ut enim ad minim veniam.</p>
    <svg class="card-arrow" width="104" height="12" viewBox="0 0 104 12"><path d="M0 6h98M92 1l8 5-8 5" stroke="#a23cff" stroke-width="2" fill="none"/></svg>
  </article>
  <article class="abs eco-card" style="left:450px">
    <svg width="60" height="60" viewBox="0 0 60 60" fill="none" stroke="#fff" stroke-width="2"><rect x="18" y="18" width="24" height="24" rx="3"/><circle cx="12" cy="12" r="7"/><circle cx="48" cy="12" r="7"/><circle cx="12" cy="48" r="7"/><circle cx="48" cy="48" r="7"/></svg>
    <h3>digital asset investing</h3>
    <p>Lorem ipsum dolor sit amet, consectetur adipiscing elit, sed do eiusmod tempor incididunt ut labore et dolore magna aliqua. Ut enim ad minim veniam.</p>
    <svg class="card-arrow" width="104" height="12" viewBox="0 0 104 12"><path d="M0 6h98M92 1l8 5-8 5" stroke="#a23cff" stroke-width="2" fill="none"/></svg>
  </article>
  <article class="abs eco-card" style="left:768px">
    <svg width="60" height="60" viewBox="0 0 60 60" fill="none" stroke="#fff" stroke-width="2"><circle cx="30" cy="24" r="16"/><text x="30" y="29" font-size="11" text-anchor="middle" fill="#fff" stroke="none" font-family="monospace">NFT</text><path d="M10 44h40v10H10z"/></svg>
    <h3>NFT</h3>
    <p>Lorem ipsum dolor sit amet, consectetur adipiscing elit, sed do eiusmod tempor incididunt ut labore et dolore magna aliqua. Ut enim ad minim veniam.</p>
    <svg class="card-arrow" width="104" height="12" viewBox="0 0 104 12"><path d="M0 6h98M92 1l8 5-8 5" stroke="#a23cff" stroke-width="2" fill="none"/></svg>
  </article>
  <div class="abs round-arrow" style="left:105px;top:332px"><svg width="12" height="12" viewBox="0 0 12 12"><path d="M8 1L3 6l5 5" stroke="#1d0b3a" stroke-width="2" fill="none"/></svg></div>
  <div class="abs round-arrow" style="left:1055px;top:332px"><svg width="12" height="12" viewBox="0 0 12 12"><path d="M4 1l5 5-5 5" stroke="#1d0b3a" stroke-width="2" fill="none"/></svg></div>
</section>

<section class="section creative">
  <h2 class="abs section-title" style="top:65px">Creative Art Projects</h2>
  <p class="abs section-sub" style="top:117px">Lorem ipsum dolor sit amet, consectetur adipiscing elit, sed do eiusmod tempor incididunt ut labore et dolore magna aliqua. Ut enim ad minim veniam.</p>
  <div class="abs side-label" style="left:40px">ART</div>
  <div class="abs side-label" style="left:1087px">MUSIC</div>
  <h3 class="abs" style="left:155px;width:365px;top:262px;text-align:center;font-family:var(--pixel);font-weight:700;font-size:42px">GAMING</h3>
  <p class="abs" style="left:155px;width:365px;top:323px;text-align:center;font-size:12.5px;line-height:24px;color:var(--muted)">Lorem ipsum dolor sit amet, consectetur adipi scing elit, sed do eiusmod tempor incididunt ut labore et dolore magna aliqua. Ut enim ad minim veniam.Lorem ipsum dolor sit amet, consectetur adipiscing elit, sed do eiusmod tempor incid idunt ut labore et dolore magna aliqua. Ut enim ad minim veniam.</p>
  <div class="placeholder" role="img" aria-label="Pixel platform game scene with clouds, coins and hearts" style="left:600px;top:228px;width:447px;height:310px;background:linear-gradient(#6fb8f0 0%,#a9dbff 70%,#7a5a3a 82%,#5a3d25 100%)"></div>
  <div class="abs dot" style="left:590px;background:#fff"></div>
  <div class="abs dot" style="left:612px;background:#3a2560"></div>
</section>

<section class="section" style="top:1905px;height:750px;background:var(--night)">
  <h2 class="abs section-title" style="top:88px">NFT Education</h2>
  <p class="abs section-sub" style="top:140px">Lorem ipsum dolor sit amet, consectetur adipiscing elit, sed do eiusmod tempor incididunt ut labore et dolore magna aliqua. Ut enim ad minim veniam.</p>
  <div class="placeholder" role="img" aria-label="Pixel art neon city at night, video with play button" style="left:183px;top:223px;width:835px;height:420px;border-radius:12px;background:linear-gradient(#3a2a7a 0%,#6a3f9a 45%,#2c2470 75%,#1c1850 100%)"></div>
  <div class="abs" style="left:556px;top:410px;width:90px;height:46px;border-radius:23px;background:#f2b21a;display:flex;align-items:center;justify-content:center">
    <svg width="30" height="30" viewBox="0 0 30 30"><circle cx="15" cy="15" r="14" fill="#fff"/><path d="M12 9l9 6-9 6z" fill="#f2b21a"/></svg>
  </div>
  <div class="abs round-arrow" style="left:160px;top:415px"><svg width="12" height="12" viewBox="0 0 12 12"><path d="M8 1L3 6l5 5" stroke="#1d0b3a" stroke-width="2" fill="none"/></svg></div>
  <div class="abs round-arrow" style="left:998px;top:415px"><svg width="12" height="12" viewBox="0 0 12 12"><path d="M4 1l5 5-5 5" stroke="#1d0b3a" stroke-width="2" fill="none"/></svg></div>
</section>

<section class="section tutorial">
  <h2 class="abs section-title" style="top:75px">Art PixelHarbor Tutorial</h2>
  <p class="abs section-sub" style="top:127px">Lorem ipsum dolor sit amet, consectetur adipiscing elit, sed do eiusmod tempor incididunt ut labore et dolore magna aliqua. Ut enim ad minim veniam.</p>

  <article class="abs tut-card" style="left:130px">
    <div class="tut-media" role="img" aria-label="Pixel art snowy mountains and pine forest" style="background:linear-gradient(#3fa0b8,#6fc6c8 45%,#1f5a4a 75%,#123a30)"></div>
    <div class="tut-body">
      <div class="tut-tier">Free</div>
      <h4>Lorem ipsum dolor sit amet consectetur adipiscing.</h4>
      <p>Lorem ipsum dolor sit amet, consectetur adipiscing elit, sed do eiusmod tempor incididunt.</p>
      <div class="socials"><span>Huddlex</span><span>Wirepost</span><span>Chirplo</span><span>Snapmora</span></div>
    </div>
  </article>
  <article class="abs tut-card" style="left:450px">
    <div class="tut-media" role="img" aria-label="Pixel art purple night city skyline" style="background:linear-gradient(#2a1455,#4a1f80 50%,#1a0b36)"><div class="ribbon"><span>OFFER<br>20%</span></div></div>
    <div class="tut-body">
      <div class="tut-tier">Paid</div>
      <h4>Lorem ipsum dolor sit amet consectetur adipiscing.</h4>
      <p>Lorem ipsum dolor sit amet, consectetur adipiscing elit, sed do eiusmod tempor incididunt.</p>
      <div class="socials"><span>Huddlex</span><span>Wirepost</span><span>Chirplo</span><span>Snapmora</span></div>
    </div>
  </article>
  <article class="abs tut-card" style="left:768px">
    <div class="tut-media" role="img" aria-label="Pixel art green hills under a cloudy sky" style="background:linear-gradient(#6aa8e0,#cfe6f5 40%,#8fb850 65%,#4c7a30)"><div class="ribbon"><span>OFFER<br>20%</span></div></div>
    <div class="tut-body">
      <div class="tut-tier">Paid</div>
      <h4>Lorem ipsum dolor sit amet consectetur adipiscing.</h4>
      <p>Lorem ipsum dolor sit amet, consectetur adipiscing elit, sed do eiusmod tempor incididunt.</p>
      <div class="socials"><span>Huddlex</span><span>Wirepost</span><span>Chirplo</span><span>Snapmora</span></div>
    </div>
  </article>
  <div class="abs" style="left:1116px;top:364px;width:8px;height:8px;border-radius:50%;background:var(--violet-bright)"></div>
  <div class="abs" style="left:1117px;top:384px;width:6px;height:6px;border-radius:50%;background:#3a2560"></div>
  <div class="abs" style="left:1117px;top:400px;width:6px;height:6px;border-radius:50%;background:#3a2560"></div>
</section>

<section class="section digital">
  <div class="placeholder" role="img" aria-label="Faint pixel ghost decoration" style="left:30px;top:0;width:215px;height:170px;background:#21103f;border-radius:0 0 10px 10px"></div>
  <div class="placeholder" role="img" aria-label="Faint pixel ghost decoration" style="left:968px;top:220px;width:200px;height:235px;background:#21103f;border-radius:95px 95px 8px 8px"></div>
  <h2 class="abs section-title" style="top:75px">Digital Asset Education</h2>
  <p class="abs" style="left:195px;width:810px;top:136px;text-align:center;font-size:12.5px;line-height:24px;color:var(--muted)">Lorem ipsum dolor sit amet, consectetur adipiscing elit, sed do eiusmod tempor incididunt ut labore et dolore magna aliqua. Ut enim ad minim veniam.Lorem ipsum dolor sit amet, consectetur adipiscing elit, sed do eiusmod tempor incididunt ut labore et dolore magna aliqua. Ut enim ad minim veniam, quis nostrud exercitation ullamco laboris nisi ut aliquip ex ea commodo consequat. Duis aute irure dolor in reprehenderit in voluptate velit esse cillum dolore eu fugiat nulla pariatur. Excepteur sint occaecat cupidatat non proident, sunt in culpa qui officia deserunt mollit.</p>
  <a class="abs btn btn-primary">CHECK YOUR RESULT</a>
  <a class="abs btn btn-outline">BLOG</a>
</section>

<footer class="section site-footer">
  <div class="abs footer-brand" style="left:0;width:1200px;text-align:center;top:70px">PixelHarbor Rangers</div>
  <nav class="abs footer-nav"><span>HOME</span><span>PHR ECOSYSTEM</span><span>NFT ART</span><span>EDUCATION &amp; NFT</span><span>BLOG</span><span>CONTACT</span></nav>
  <div class="abs pay-row"><span class="pay-chip">Payvia</span><span class="pay-chip">Cardello</span><span class="pay-chip">Findsy</span><span class="pay-chip">Amberpay</span></div>
  <div class="abs wallet-row"><span><i></i>VeloPurse</span><span><i></i>Kindle Vault</span></div>
  <p class="abs copyright">© copyrights 2022 <em>PixelHarbor Rangers</em><br>All Rights Reserved</p>
</footer>

</body>
</html>
```